MyName is TapLedger .... Killer of Business Cards!!! WANT a KickAss Design Landing Page :)

How 'TapLedger' works:
- with a unique name for each country, like a personalise car plate number
- our platform links through a 'Quick Text' keyword short code
- TapLedger platform will respond with downloaded ready full contact business file link
- this is designed to be downloaded in just '3 clicks' into your Contacts Folder
- any changes,,updates, images, online profiles can be made in real time updates
- TapLedger provides a backend login to manage individual account and is ready
Enterprise model for larger staff companies
- platform is international ready and have launched
Australia, in September 2019.

Yes, your whole business card and online profile in '3' simple clicks. No '20-30 mins' of typing the business card contacts details into mobile phones.
** Fact: 88% of business cards are lost of thrown out within 7 days.
(https://www.plumfinchstats.com/business-card-statistics.html) **

NZ ClipStream
https://vidhost.example/q7Rt2LmP9xZ

**current websites are www.tapledge.co.nz www.taplink.com.au www.tapledgerau.com www.tapledgerus.com **

Target Market(s)

Anybody who uses a business card, from trades person, real estate agents, consultants, bankers (in NZ/AU with have plumbers, financial advisors, real estate agents, mortgage brokers, sports agents, Telcos etc etc)

Industry/Entity Type

Business Software

Coding

Coded - Design and coding required

Number of Pages Required

4 page

Font styles to use
Other font styles liked:
• libre franklin black

Requirements
Must have
• TapLedger a simple 'in delivery' and smart 'in innovation' solution so our message is Simple, Clear and Inquisitive. We would like a converting landing page because we are selling Nimble Cloud Suite at low-entry cost and no-contract. IWe want to direct clients to a name reservation platform to a virtual business card that uses our Nimble Core Engine. We will require some code at the back to link the name reservation and sign up source code(javascript). This web/landing page fresh page is required because we have recently changed our marketing strategy to be purely digital marketing in Chatterbook and Snapgrid Ads from now on. We would like this to be exciting graphically to grab attention, inquisitive enough to check your name availability and follow through with call to action with the right colours and graphics images. We plan to test the right pitch offering until we get the markets feedback on the best offering/re-design and then push harder with more CB and SG Ads. ( **we plan to continue multiple regular campaigns as the business has now change our strategy due to covid-19 and we will focus mainly on direct to consumers**)

Also:
2 buttons: Signup and a Check availability little form to allow a java script to be added/HTML5/CB advertising/Super Inviting to check 'YOUR UNIQUE NAME' is available. Then clicking the to reserve the name to purchase our Quick Text/Eco-Friendly/Relevant to todays tech and Low Cost service. We will be offering Promo codes for each campaign.
No Apps. Works with SMS, any smartphone, country specific, enterprise ready, and CONTACTLESS ....
Nice to have
• Personal feeling. Unique choice of 'your name' as this is your business and social profile in one. Strong independent images and confident to share with anybody their profile by just sharing their name.
Should not have
• Open currently....

```html
<!DOCTYPE html>
<html lang="en">
<head>
<meta charset="utf-8">
<title>TapLedger – Virtual Business Card</title>
<link rel="stylesheet" href="https://fonts.googleapis.com/css2?family=Libre+Franklin:wght@400;500;600;700;800;900&display=swap">
<style>
:root{
  --teal:#1a9ea3;
  --teal-dark:#137f86;
  --navy:#1d3a6a;
  --navy-deep:#172e55;
  --ink:#27344a;
  --muted:#6b7686;
  --line:#e3e7ee;
  --soft:#f1f3f7;
  --white:#ffffff;
}
*{box-sizing:border-box;margin:0;padding:0}
html,body{width:1200px;height:3380px;overflow:hidden}
body{font-family:"Libre Franklin",Arial,sans-serif;color:var(--ink);background:var(--white);position:relative}
.btn{display:inline-block;border:none;border-radius:22px;font-family:inherit;font-weight:700;font-size:13px;letter-spacing:.5px;text-transform:uppercase;color:var(--white);background:var(--navy);padding:13px 26px;white-space:nowrap}
.btn--teal{background:var(--teal)}
.brand{display:flex;align-items:center;gap:10px;font-weight:800;color:var(--navy)}
.brand__dot{width:30px;height:30px;border-radius:50%;background:var(--teal)}

/* header */
.site-header{position:absolute;top:0;left:0;width:1200px;height:90px;display:flex;align-items:center;justify-content:space-between;padding:0 70px;z-index:3}
.site-header .brand{font-size:28px}
.nav{display:flex;align-items:center;gap:26px;font-size:13px;font-weight:700;color:var(--navy);letter-spacing:.4px}
.nav__link--active{background:var(--soft);color:var(--teal);padding:8px 12px;border-radius:4px}
.nav .btn{padding:11px 22px;font-size:12px}

/* hero */
.hero{position:absolute;top:0;left:0;width:1200px;height:740px;background:linear-gradient(180deg,#ffffff 0%,#f4f6f9 100%);overflow:hidden}
.hero__copy{position:absolute;left:70px;top:190px;width:560px}
.hero__title{font-size:31px;line-height:1.25;font-weight:900;color:var(--teal);text-transform:uppercase}
.hero__title span{color:var(--navy)}
.hero__copy .btn{margin-top:30px}
.hero__visual{position:absolute;left:700px;top:100px;width:400px;height:460px;border-radius:24px;background:radial-gradient(circle at 55% 40%,#2aa6ab 0%,#1d6f87 45%,#d9dfe7 100%)}
.hero__wave{position:absolute;left:0;bottom:0;width:1200px;height:170px}

/* intro / video */
.intro{position:absolute;top:740px;left:0;width:1200px;height:500px}
.intro__video{position:absolute;left:130px;top:90px;width:460px;height:290px;border-radius:6px;background:linear-gradient(135deg,#5a6a82 0%,#2d3d57 60%,#1a9ea3 100%);display:flex;align-items:center;justify-content:center}
.play{width:74px;height:74px;border-radius:50%;background:rgba(255,255,255,.92);display:flex;align-items:center;justify-content:center}
.intro__text{position:absolute;left:640px;top:100px;width:450px}
.intro__kicker{font-size:24px;font-weight:600;color:var(--teal)}
.intro__title{font-size:36px;font-weight:900;color:var(--navy);line-height:1.15;margin-top:4px}
.intro__try{font-size:21px;color:var(--teal);font-weight:600;margin-top:14px}
.intro__body{font-size:14px;line-height:1.6;color:var(--muted);margin-top:10px}
.intro__body strong{color:var(--ink)}
.check{display:flex;gap:10px;margin-top:22px}
.check__input{width:230px;height:44px;border:1px solid var(--line);border-radius:22px;padding:0 20px;font-family:inherit;font-size:13px;color:var(--muted);background:var(--white)}
.check .btn{padding:0 20px;height:44px;line-height:44px;font-size:12px}

/* benefits */
.benefits{position:absolute;top:1240px;left:0;width:1200px;height:700px}
.benefits__bg{position:absolute;inset:0}
.section-head{position:relative;text-align:center;color:var(--navy)}
.section-head__small{font-size:22px;font-weight:500}
.section-head__big{font-size:36px;font-weight:800;margin-top:2px}
.benefits .section-head{padding-top:120px}
.benefit-grid{position:relative;width:860px;margin:50px auto 0;display:grid;grid-template-columns:1fr 1fr;gap:22px}
.benefit{background:var(--white);border-radius:8px;box-shadow:0 4px 16px rgba(29,58,106,.08);padding:24px 22px;display:flex;gap:18px;align-items:flex-start;height:112px}
.benefit__icon{flex:0 0 56px;height:56px;border-radius:50%;background:var(--teal);display:flex;align-items:center;justify-content:center}
.benefit__title{font-size:15px;font-weight:800;color:var(--teal);text-transform:uppercase;letter-spacing:.5px}
.benefit__text{font-size:12.5px;line-height:1.55;color:var(--muted);margin-top:6px}

/* plans */
.plans{position:absolute;top:1940px;left:0;width:1200px;height:560px}
.plans__copy{position:absolute;left:100px;top:90px;width:440px}
.plans__kicker{font-size:24px;color:var(--teal);font-weight:600}
.plans__title{font-size:38px;font-weight:900;color:var(--navy);margin-top:2px}
.plans__lead{font-size:16px;color:var(--teal);font-weight:600;margin-top:14px;line-height:1.45}
.plans__body{font-size:13.5px;line-height:1.65;color:var(--muted);margin-top:16px}
.plans__copy .btn{margin-top:28px}
.plan{position:absolute;width:250px;background:var(--white);border-radius:8px;box-shadow:0 8px 26px rgba(29,58,106,.14);overflow:hidden;text-align:center}
.plan--personal{left:600px;top:100px;height:340px}
.plan--business{left:880px;top:70px;height:380px}
.plan__head{height:64px;display:flex;align-items:center;justify-content:center;color:var(--white);font-weight:800;font-size:16px;letter-spacing:.6px}
.plan--personal .plan__head{background:var(--teal)}
.plan--business .plan__head{background:var(--navy)}
.plan__icon{margin:36px auto 0;width:50px;height:50px}
.plan__text{font-size:13px;line-height:1.55;color:var(--muted);padding:18px 28px 0}
.plan .btn{margin-top:22px;padding:12px 20px;font-size:11px}

/* testimonials */
.testimonials{position:absolute;top:2500px;left:0;width:1200px;height:560px}
.testimonials__bg{position:absolute;inset:0}
.testimonials .section-head{color:var(--white);padding-top:100px}
.quotes{position:relative;display:flex;gap:40px;justify-content:center;margin-top:40px}
.quote{width:420px;height:250px;background:var(--white);border-radius:6px;padding:30px 28px;display:flex;gap:18px}
.quote__mark{font-size:70px;line-height:.8;font-weight:900;color:var(--navy);font-family:Georgia,"Times New Roman",serif}
.quote__name{font-size:16px;font-weight:800;color:var(--navy);text-transform:uppercase;letter-spacing:.5px}
.quote__text{font-size:12.5px;line-height:1.6;color:var(--muted);margin-top:8px}
.quote__role{font-size:12.5px;color:var(--teal);margin-top:10px;line-height:1.5}
.arrow{position:absolute;top:320px;width:30px;height:30px}
.arrow--prev{left:80px}
.arrow--next{right:80px}

/* footer */
.site-footer{position:absolute;top:3060px;left:0;width:1200px;height:320px}
.contacts{position:absolute;left:120px;top:40px;list-style:none}
.contacts li{display:flex;align-items:center;gap:16px;margin-bottom:22px}
.contacts__icon{width:40px;height:40px;border-radius:50%;background:var(--navy);display:flex;align-items:center;justify-content:center;flex:0 0 40px}
.contacts__label{font-size:14px;font-weight:700;color:var(--navy)}
.contacts__value{font-size:13px;color:var(--muted);margin-top:2px}
.site-footer .brand{position:absolute;right:140px;top:70px;font-size:54px;gap:18px}
.site-footer .brand__dot{width:60px;height:60px}
.footer__wave{position:absolute;left:0;top:200px;width:1200px;height:70px}
.footer__bar{position:absolute;left:0;bottom:0;width:1200px;height:60px;background:var(--navy-deep);display:flex;align-items:center;justify-content:space-between;padding:0 70px;color:#cfd7e6;font-size:13px}
.social{display:flex;gap:10px;align-items:center}
.social span{width:30px;height:30px;border-radius:50%;border:1px solid #cfd7e6;display:flex;align-items:center;justify-content:center;font-size:10px;font-weight:700;color:#fff}
.social .social__code{border:none;width:auto}
</style>
</head>
<body>

<section class="hero">
  <div class="hero__copy">
    <h1 class="hero__title">Instantly <span>share</span> all your<br><span>business contact</span> details<br>with 1 <span>'Quick'</span> text</h1>
    <span class="btn">Read more</span>
  </div>
  <div class="hero__visual" role="img" aria-label="Hand holding a smartphone showing a promo code offer"></div>
  <svg class="hero__wave" viewBox="0 0 1200 170" preserveAspectRatio="none" aria-hidden="true">
    <path d="M0 60 C260 170 620 150 1200 40 L1200 170 L0 170 Z" fill="#1a9ea3"/>
    <path d="M0 95 C300 180 700 160 1200 70 L1200 170 L0 170 Z" fill="#1d3a6a"/>
    <path d="M0 135 C320 200 760 175 1200 120 L1200 170 L0 170 Z" fill="#ffffff"/>
  </svg>
</section>

<header class="site-header">
  <div class="brand"><span class="brand__dot"></span>TapLedger</div>
  <nav class="nav">
    <span class="nav__link--active">HOME</span>
    <span>PARTNERS</span>
    <span>BENEFITS</span>
    <span>PLANS</span>
    <span>TESTIMONIALS</span>
    <span>LOG IN</span>
    <span class="btn">Signup</span>
  </nav>
</header>

<section class="intro">
  <div class="intro__video" role="img" aria-label="Video still: business cards are over, see what's in">
    <div class="play"><svg width="28" height="28" viewBox="0 0 24 24"><path d="M7 4 L20 12 L7 20 Z" fill="#1d3a6a"/></svg></div>
  </div>
  <div class="intro__text">
    <p class="intro__kicker">No more business cards,</p>
    <h2 class="intro__title">That's So Unique And Cool.</h2>
    <p class="intro__try">Try it now. Txt 'TapLedger' to 0400 555 018</p>
    <p class="intro__body">Pretty cool right.. Get Your Quick Text code instantly.<br><strong>TapLedger - Simple, Low Cost, Smart and Effective! Click below to reserve.</strong></p>
    <div class="check">
      <input class="check__input" type="text" placeholder="Your Keyword">
      <span class="btn">Check availability</span>
    </div>
  </div>
</section>

<section class="benefits">
  <svg class="benefits__bg" viewBox="0 0 1200 700" preserveAspectRatio="none" aria-hidden="true">
    <path d="M0 40 C400 0 800 0 1200 60 L1200 700 L0 700 Z" fill="#f1f3f7"/>
  </svg>
  <div class="section-head">
    <p class="section-head__small">Our</p>
    <h2 class="section-head__big">Simple Benefits Are</h2>
  </div>
  <div class="benefit-grid">
    <div class="benefit">
      <div class="benefit__icon"><svg width="26" height="26" viewBox="0 0 24 24" fill="none" stroke="#fff" stroke-width="2"><circle cx="12" cy="10" r="6"/><path d="M9 20h6M10 16v4M14 16v4"/></svg></div>
      <div><h3 class="benefit__title">Logical</h3><p class="benefit__text">Everybody has a mobile phone and every phone can text.</p></div>
    </div>
    <div class="benefit">
      <div class="benefit__icon"><svg width="26" height="26" viewBox="0 0 24 24" fill="none" stroke="#fff" stroke-width="2"><circle cx="12" cy="8" r="4"/><path d="M4 21c1-5 15-5 16 0"/></svg></div>
      <div><h3 class="benefit__title">Professional</h3><p class="benefit__text">Your customers, potential customers will be impressed with your innovation.</p></div>
    </div>
    <div class="benefit">
      <div class="benefit__icon"><svg width="26" height="26" viewBox="0 0 24 24" fill="none" stroke="#fff" stroke-width="2"><ellipse cx="12" cy="6" rx="7" ry="3"/><path d="M5 6v12c0 2 14 2 14 0V6M5 12c0 2 14 2 14 0"/></svg></div>
      <div><h3 class="benefit__title">Data Safe</h3><p class="benefit__text">All data is held on a secure cloud server hosted in Sydney, with daily backups.</p></div>
    </div>
    <div class="benefit">
      <div class="benefit__icon"><svg width="26" height="26" viewBox="0 0 24 24" fill="none" stroke="#fff" stroke-width="2"><rect x="5" y="11" width="14" height="10" rx="2"/><path d="M8 11V7a4 4 0 0 1 8 0v4"/></svg></div>
      <div><h3 class="benefit__title">Secure Payment</h3><p class="benefit__text">Backed by a trusted global payment gateway certified to PCI Level One standards.</p></div>
    </div>
    <div class="benefit">
      <div class="benefit__icon"><svg width="26" height="26" viewBox="0 0 24 24" fill="none" stroke="#fff" stroke-width="2"><path d="M5 19C5 9 12 5 20 4c-1 8-5 15-15 15zM5 19l8-8"/></svg></div>
      <div><h3 class="benefit__title">Environment</h3><p class="benefit__text">No cost of business cards, no more paper waste, no reprinting.</p></div>
    </div>
    <div class="benefit">
      <div class="benefit__icon"><svg width="26" height="26" viewBox="0 0 24 24" fill="none" stroke="#fff" stroke-width="2.4"><path d="M5 12l5 5 9-10"/></svg></div>
      <div><h3 class="benefit__title">Ease</h3><p class="benefit__text">So simple to share and retrieve your TapLedger card.</p></div>
    </div>
  </div>
</section>

<section class="plans">
  <div class="plans__copy">
    <p class="plans__kicker">With great pricing</p>
    <h2 class="plans__title">Plans For Everyone</h2>
    <p class="plans__lead">G'Day Australia,<br>'Virtual Business Card' or 'TapLedger' is the Digital Solution.</p>
    <p class="plans__body">TapLedger is the intelligent, relevant and easy way for your new customers or friends to receive ALL of your contact details in a few clicks, no typing needed. This can be done anytime and anywhere, all within Australia.</p>
    <span class="btn">Read more</span>
  </div>
  <div class="plan plan--personal">
    <div class="plan__head">PERSONAL PLAN</div>
    <svg class="plan__icon" viewBox="0 0 24 24" fill="none" stroke="#1a9ea3" stroke-width="1.6"><rect x="3" y="5" width="18" height="14" rx="2"/><circle cx="9" cy="11" r="2.2"/><path d="M5.5 16.5c.8-2.4 6.2-2.4 7 0M14 10h5M14 13h4"/></svg>
    <p class="plan__text">Provides for one personal and one personal Card for $4.99 + gst / month</p>
    <span class="btn">Get started</span>
  </div>
  <div class="plan plan--business">
    <div class="plan__head">BUSINESS PLAN</div>
    <svg class="plan__icon" viewBox="0 0 24 24" fill="none" stroke="#1d3a6a" stroke-width="1.6"><rect x="4" y="3" width="12" height="16" rx="1"/><path d="M7 7h6M7 10h6M7 13h4"/><rect x="10" y="9" width="10" height="12" rx="1" fill="#fff"/><path d="M12.5 13h5M12.5 16h5"/></svg>
    <p class="plan__text">Provides for one personal and business Account for $6.99 + gst / month</p>
    <span class="btn">Get started</span>
  </div>
</section>

<section class="testimonials">
  <svg class="testimonials__bg" viewBox="0 0 1200 560" preserveAspectRatio="none" aria-hidden="true">
    <defs><linearGradient id="band" x1="0" y1="0" x2="1" y2="0"><stop offset="0" stop-color="#1a9ea3"/><stop offset="1" stop-color="#1d3a6a"/></linearGradient></defs>
    <path d="M0 70 C350 0 850 0 1200 60 L1200 470 C850 540 350 540 0 480 Z" fill="url(#band)"/>
  </svg>
  <div class="section-head">
    <p class="section-head__small">Our</p>
    <h2 class="section-head__big">Our Clients Love Us!</h2>
  </div>
  <svg class="arrow arrow--prev" viewBox="0 0 24 24" fill="none" stroke="#fff" stroke-width="2.4"><path d="M15 5l-7 7 7 7"/></svg>
  <svg class="arrow arrow--next" viewBox="0 0 24 24" fill="none" stroke="#fff" stroke-width="2.4"><path d="M9 5l7 7-7 7"/></svg>
  <div class="quotes">
    <article class="quote">
      <div class="quote__mark">&ldquo;</div>
      <div>
        <h3 class="quote__name">Mara Whitfield</h3>
        <p class="quote__text">The service gathered by our team has saved us so much time over the past year. For me it is the best and most powerful tool available for the Real Estate industry, I often get caught out in suburbs and cafes.</p>
        <p class="quote__role">Licensed Salesperson,<br>Brightwater Realty Limited</p>
      </div>
    </article>
    <article class="quote">
      <div class="quote__mark">&ldquo;</div>
      <div>
        <h3 class="quote__name">Owen Calder</h3>
        <p class="quote__text">At Harbourline Mortgages &amp; Insurance, we have found TapLedger to be an excellent tool for sharing our contact details. Simply asking them to text our keyword means clients always have our latest details at hand, which feels professional.</p>
        <p class="quote__role">Managing Director, Harbourline<br>Mortgages</p>
      </div>
    </article>
  </div>
</section>

<footer class="site-footer">
  <ul class="contacts">
    <li>
      <span class="contacts__icon"><svg width="18" height="18" viewBox="0 0 24 24" fill="none" stroke="#fff" stroke-width="2"><path d="M12 22s7-7 7-12a7 7 0 0 0-14 0c0 5 7 12 7 12z"/><circle cx="12" cy="10" r="2.5"/></svg></span>
      <div><p class="contacts__label">Address:</p><p class="contacts__value">PO Box 4120 Coral Bay QLD</p></div>
    </li>
    <li>
      <span class="contacts__icon"><svg width="18" height="18" viewBox="0 0 24 24" fill="none" stroke="#fff" stroke-width="2"><rect x="3" y="6" width="18" height="12" rx="1"/><path d="M3 7l9 6 9-6"/></svg></span>
      <div><p class="contacts__label">Mail:</p><p class="contacts__value">support@tapledger.example</p></div>
    </li>
    <li>
      <span class="contacts__icon"><svg width="18" height="18" viewBox="0 0 24 24" fill="none" stroke="#fff" stroke-width="2"><path d="M5 4h4l2 5-2.5 1.5a11 11 0 0 0 5 5L15 13l5 2v4a2 2 0 0 1-2 2A16 16 0 0 1 3 6a2 2 0 0 1 2-2z"/></svg></span>
      <div><p class="contacts__label">Phone:</p><p class="contacts__value">+61 7 5550 0142</p></div>
    </li>
  </ul>
  <div class="brand"><span class="brand__dot"></span>TapLedger</div>
  <svg class="footer__wave" viewBox="0 0 1200 70" preserveAspectRatio="none" aria-hidden="true">
    <path d="M0 30 C400 80 800 -10 1200 30 L1200 70 L0 70 Z" fill="#172e55"/>
  </svg>
  <div class="footer__bar">
    <p>Copyrights @ 2020 TapLedger. All Rights Reserved.</p>
    <div class="social"><span>CB</span><span>SG</span><span>CS</span><span class="social__code">C20</span></div>
  </div>
</footer>

</body>
</html>
```